'Little Lantern' promotional brochure

We have designed a 6 week program to educate impending first-time parents about the things they need to know to survive the first 6 months. Sessions delivered by general practitioner/family doctor, dietician, physiotherapist, speech pathologist and psychologist. Our promotional blurb is: 'A comprehensive education program for first-time parents-to-be, delivered over 6 weeks by health professionals in your community, about everything you need to know to look after your baby (and yourself!) in the first 6 months'. I now want to put together a promotional brochure to be distributed to those couples who express an interest which will provide further details of what will be delivered in the course.
Updates
In terms of layout, I envisaged a double sided A4 size, foldable into 3 sections, but very happy to be guided on this.
Target Market(s)
To appeal to a young, well educated demographic. First time parents couples.
Industry/Entity Type
Medical
Font styles to use
Other font styles liked:
- Playfair Display
Requirements
Must have
- Playfair display font to be consistent with our logo (attached). Logo also included please. Some consistency with colours of logo please.
Nice to have
- I am a doctor, and have no creative genes! But prefer a clean and professional appearance overall. Not too cluttered in overall appearance.
Should not have
- No cheesy pictures of babies.

```html
<!DOCTYPE html>
<html lang="en">
<head>
<meta charset="utf-8">
<title>Little Lantern – Program Flyer</title>
<link rel="stylesheet" href="https://fonts.googleapis.com/css2?family=Lato:wght@300;400;700;900&family=Montserrat:wght@700&display=swap">
<style>
  :root {
    --green: #6abf45;
    --grey-panel: #e6e6e6;
    --text: #555555;
    --title-grey: #5a5a5a;
    --quote-dark: #333333;
    --page-bg: #e9e9e9;
    --white: #ffffff;
  }
  * { margin: 0; padding: 0; box-sizing: border-box; }
  html, body { width: 1200px; height: 1200px; overflow: hidden; background: var(--page-bg); }
  .flyer {
    position: absolute; left: 185px; top: 18px;
    width: 922px; height: 1293px;
    transform: scale(0.9); transform-origin: 0 0;
    background: var(--white); overflow: hidden;
    font-family: "Lato", sans-serif; color: var(--text);
    box-shadow: 0 4px 18px rgba(0,0,0,0.18);
  }
  .shapes { position: absolute; inset: 0; }
  .brand { position: absolute; left: 55px; top: 100px; display: flex; align-items: center; gap: 12px; }
  .brand-mark { width: 26px; height: 26px; background: var(--green); }
  .brand-name { font-family: "Lato", sans-serif; font-weight: 400; font-size: 24px; line-height: 26px; color: var(--title-grey); }
  .title { position: absolute; left: 72px; top: 178px; }
  .title-light { display: block; font-weight: 300; font-size: 70px; line-height: 74px; color: var(--title-grey); }
  .title-bold { display: block; font-weight: 700; font-size: 70px; line-height: 80px; color: var(--green); }
  .quote { position: absolute; font-family: "Lato", sans-serif; font-weight: 900; font-size: 64px; line-height: 64px; color: var(--quote-dark); }
  .quote.open { left: 44px; top: 175px; }
  .quote.close { left: 326px; top: 252px; }
  .week-tab {
    position: absolute; height: 53px; background: var(--green); color: var(--white);
    font-family: "Montserrat", sans-serif; font-weight: 700; font-size: 34px; line-height: 53px;
  }
  .week-tab.left { left: 0; border-radius: 0 16px 16px 0; padding-left: 30px; }
  .week-tab.right { right: 0; border-radius: 16px 0 0 16px; padding-left: 25px; }
  .copy { position: absolute; font-size: 14.8px; line-height: 18px; letter-spacing: -0.1px; hyphens: auto; -webkit-hyphens: auto; }
  .copy p + p { margin-top: 18px; }
  .copy.justify p { text-align: justify; }
  .copy.right { text-align: right; }
  .copy.right.justify p { text-align: justify; text-align-last: right; }
  .bullets { list-style: none; }
  .bullets.lead li::before { content: "•"; color: var(--green); position: absolute; margin-left: -13px; }
  .bullets.trail li::after { content: " •"; color: var(--green); }
  .contact { position: absolute; right: 30px; top: 1176px; text-align: right; color: var(--white); font-size: 15px; line-height: 18.5px; }
  .contact li { list-style: none; display: flex; justify-content: flex-end; align-items: center; gap: 8px; }
  .contact svg { width: 12px; height: 12px; }
  .contact .no-icon { padding-right: 20px; }
</style>
</head>
<body>
<article class="flyer">
  <svg class="shapes" width="922" height="1293" viewBox="0 0 922 1293">
    <defs>
      <radialGradient id="photoTone" cx="55%" cy="45%" r="60%">
        <stop offset="0" stop-color="#f3cdb3"/>
        <stop offset="0.6" stop-color="#e3ac8f"/>
        <stop offset="1" stop-color="#7a4a3c"/>
      </radialGradient>
    </defs>
    <path d="M435 380 L922 380 L922 1293 L435 1293 Z" fill="var(--grey-panel)"/>
    <path d="M380 1293 C520 1190 720 1155 922 1150 L922 1293 Z" fill="var(--green)"/>
    <circle cx="650" cy="168" r="336" fill="var(--green)"/>
    <circle cx="668" cy="160" r="326" fill="var(--white)"/>
    <circle cx="672" cy="158" r="322" fill="url(#photoTone)" role="img" aria-label="Photo of a mother gently holding her newborn baby close"/>
  </svg>

  <header class="brand">
    <span class="brand-mark"></span>
    <span class="brand-name">Wattlebrook Health</span>
  </header>

  <span class="quote open">‘</span>
  <h1 class="title">
    <span class="title-light">Little</span>
    <span class="title-bold">Lantern</span>
  </h1>
  <span class="quote close" style="left:370px;">’</span>

  <h2 class="week-tab left" style="top:382px;width:185px;">Week 1</h2>
  <div class="copy" style="left:42px;top:457px;width:340px;">
    <p>GP Dr Helen Marsh will share information for Mum’s own health after delivery. Topics include:</p>
    <ul class="bullets lead">
      <li>Vaccinations in pregnancy</li>
      <li>Bleeding, bladder and bowel after delivery</li>
      <li>Breastfeeding, engorgement and mastitis</li>
      <li>Bottle feeding</li>
      <li>Post-natal anxiety &amp; depression</li>
      <li>Intimacy and contraception</li>
    </ul>
  </div>

  <h2 class="week-tab left" style="top:612px;width:186px;">Week 2</h2>
  <div class="copy justify" style="left:26px;top:684px;width:376px;">
    <p>Session 1 – Clinical Psychologist Dr Nadia Ferris will discuss changes in relationships as couples becomes parents, gender roles in parenting and post-natal depression.</p>
    <p>Session 2 – Physiotherapist Tara Whitlock will present advice for Mums regarding exercise during and after pregnancy, looking after the pelvic floor during and after pregnancy, and abdominal muscle separation management. She will also provide advice for promoting babies’ neck strength and minimising the risk of flat spots on the head and encouraging gross motor skills in the first 6 months</p>
  </div>

  <h2 class="week-tab left" style="top:922px;width:172px;padding-left:14px;">Week 3</h2>
  <div class="copy justify" style="left:24px;top:996px;width:390px;">
    <p>Session 1 – Dietician Amy Callan provides advice for Mums regarding healthy eating during pregnancy and lactation, normal weight gain during pregnancy and realistic weight loss after. She will also discuss the evidence regarding breastfeeding VS bottle-feeding, normal infant weight gain and introducing solids (including those with potential for allergy).</p>
    <p>Session 2 – Paediatric Speech Pathologist Ruth Okafor will share information about latching and breast-feeding troubles &amp; tongue tie, advice about dummies and finger-sucking, introducing solids &amp; feeding (including ‘pouch’ food), encouraging language development and current evidence about electronic devices impacting language development.</p>
  </div>

  <h2 class="week-tab right" style="top:514px;width:192px;">Week 4</h2>
  <div class="copy right" style="left:430px;top:582px;width:465px;">
    <p>GP Dr Helen Marsh will share advice about your babies’ health<br>in the first 6 months, including:</p>
    <ul class="bullets trail">
      <li>Skin of newborns</li>
      <li>Sleeping</li>
      <li>Crying</li>
      <li>Immunisations</li>
      <li>Fever and infections</li>
      <li>Diarrhoea and constipation</li>
      <li>Teething</li>
      <li>Understanding a baby’s signals</li>
    </ul>
  </div>

  <h2 class="week-tab right" style="top:767px;width:194px;">Week 5</h2>
  <div class="copy right justify" style="left:496px;top:840px;width:401px;">
    <p>Session 1 – Clinical Psychologist Dr Nadia Ferris will share information about bonding &amp; attachment with your baby, how to promote their social &amp; emotional development and how to manage separation anxiety. She will also discuss positive parenting approaches.</p>
  </div>

  <h2 class="week-tab right" style="top:934px;width:192px;">Week 6</h2>
  <div class="copy right justify" style="left:497px;top:1003px;width:403px;">
    <p>Session 1 – Secret Men’s Business – a men-only session (including beer!) with a new father for frank discussion about the road ahead. Mums will do a shopping excursion with the GP &amp; Dietician to FreshMart to look at baby products and food – the good and the bad!</p>
    <p>Session 2 - Program review, reflection and evaluation and future session planning when baby is 6 months of age.</p>
  </div>

  <ul class="contact">
    <li>02 5550 1234
      <svg viewBox="0 0 12 12"><path d="M2 1 L4.5 1 L5.5 3.5 L4 4.6 C4.8 6.3 5.8 7.3 7.4 8 L8.5 6.5 L11 7.5 L11 10 C6 10.5 1.5 6 2 1 Z" fill="#fff"/></svg></li>
    <li>www.wattlebrookhealth.com.au
      <svg viewBox="0 0 12 12"><circle cx="6" cy="6" r="5" fill="none" stroke="#fff" stroke-width="1.4"/><path d="M1 6 H11 M6 1 C3.5 4 3.5 8 6 11 M6 1 C8.5 4 8.5 8 6 11" fill="none" stroke="#fff" stroke-width="1"/></svg></li>
    <li>reception@wattlebrookhealth.com.au
      <svg viewBox="0 0 12 12"><rect x="1" y="2.5" width="10" height="7" fill="#fff"/><path d="M1 2.5 L6 6.5 L11 2.5" fill="none" stroke="var(--green)" stroke-width="1"/></svg></li>
    <li>Wattlebrook Village, Shop 11
      <svg viewBox="0 0 12 12"><path d="M6 11.5 C3 7.5 2.5 6 2.5 4.5 A3.5 3.5 0 0 1 9.5 4.5 C9.5 6 9 7.5 6 11.5 Z" fill="#fff"/><circle cx="6" cy="4.5" r="1.3" fill="var(--green)"/></svg></li>
    <li class="no-icon">48 Wattle Way Wattlebrook NSW 2400</li>
  </ul>
</article>
</body>
</html>
```